Brimlow Plumbing Solutions

This is for my new plumbing company, I have attached an example of what I’m going for but want it to look better.

Target Market(s)

Home owners, real estate, etc.

Industry/Entity Type

Plumbing

Font styles to use
Other font styles liked:
• As per my logo and other examples uploaded

Colors

Designer to choose colors to be used in the design.

Requirements
Must have
• Must include my logo provided and similar to my flyer I have attached but better

```html
<!DOCTYPE html>
<html lang="en">
<head>
<meta charset="utf-8">
<title>Brimlow Plumbing Solutions – Flyer Set</title>
<link rel="stylesheet" href="https://fonts.googleapis.com/css2?family=Inter:wght@400;500;600;700;800&family=Oswald:wght@500;600&display=swap">
<style>
  :root {
    --navy: #173352;
    --navy-deep: #10263f;
    --navy-soft: #2a4a6b;
    --green: #7cc142;
    --green-dark: #4f8f2b;
    --white: #ffffff;
    --ink: #1b1f24;
    --stage: #ececec;
    --photo-a: #5f9a45;
    --photo-b: #22405f;
  }
  * { margin: 0; padding: 0; box-sizing: border-box; }
  html, body { width: 1200px; height: 1200px; overflow: hidden; }
  body {
    background: var(--stage);
    font-family: "Inter", "Helvetica Neue", Arial, sans-serif;
    position: relative;
  }

  .set-title {
    position: absolute; left: 55px; top: 98px;
    font-family: "Oswald", "Arial Narrow", sans-serif;
    color: var(--ink); line-height: 1.15; text-transform: uppercase;
  }
  .set-title__name { font-size: 46px; font-weight: 600; letter-spacing: 0.5px; }
  .set-title__tagline { font-size: 37px; font-weight: 500; margin-top: 8px; }

  .side-label {
    position: absolute; width: 200px; text-align: center;
    font-weight: 700; font-size: 27px; color: var(--navy); letter-spacing: 0.5px;
  }
  .side-label--front { left: 832px; top: 30px; }
  .side-label--back  { left: 832px; top: 575px; }

  .flyer {
    position: absolute; overflow: hidden; background: var(--white);
    box-shadow: 0 2px 8px rgba(0,0,0,0.18);
  }
  .flyer--main  { left: 47px;  top: 265px; width: 601px; height: 860px; }
  .flyer--front { left: 701px; top: 68px;  width: 447px; height: 498px; }
  .flyer--back  { left: 701px; top: 609px; width: 447px; height: 543px; }

  .flyer__bg { position: absolute; left: 0; top: 0; width: 100%; height: 100%; }
  .flyer__item { position: absolute; white-space: nowrap; }

  .brand { display: flex; align-items: flex-start; gap: 12px; }
  .brand__mark { background: var(--green); flex: none; }
  .brand__name { color: var(--navy); font-weight: 700; line-height: 1.05; text-transform: uppercase; }
  .brand__name span { display: block; }
  .brand__name span:last-child { color: var(--green-dark); }
  .brand--lg .brand__mark { width: 34px; height: 34px; margin-top: 4px; }
  .brand--lg .brand__name { font-size: 25px; }
  .brand--sm { gap: 9px; }
  .brand--sm .brand__mark { width: 25px; height: 25px; margin-top: 3px; }
  .brand--sm .brand__name { font-size: 18px; }

  .logo-slot { text-align: center; color: var(--navy-deep); }
  .logo-slot__word { font-weight: 800; letter-spacing: 0.02em; }
  .logo-slot__sub { font-weight: 500; letter-spacing: 0.08em; color: var(--green-dark); text-transform: uppercase; margin-top: 2px; }
  .logo-slot--lg .logo-slot__word { font-size: 26px; }
  .logo-slot--lg .logo-slot__sub { font-size: 7.5px; }
  .logo-slot--sm .logo-slot__word { font-size: 19px; }
  .logo-slot--sm .logo-slot__sub { font-size: 5.5px; }

  .headline { color: var(--white); font-weight: 700; }
  .headline--lg { font-size: 46px; line-height: 56px; }
  .headline--sm { font-size: 35px; line-height: 42px; }

  .subhead { color: var(--green); font-weight: 600; }
  .subhead--lg { font-size: 35px; }
  .subhead--sm { font-size: 27px; }

  .services { list-style: none; color: var(--white); }
  .services li::before {
    content: ""; display: inline-block; width: 5px; height: 5px;
    border-radius: 50%; background: var(--green); margin-right: 8px; vertical-align: 3px;
  }
  .services li.services__cont::before { background: transparent; }
  .services--lg { font-size: 19px; line-height: 26px; }
  .services--front { font-size: 14px; line-height: 18px; }
  .services--back { font-size: 16px; line-height: 23.5px; }
  .services--front li::before, .services--back li::before { width: 4px; height: 4px; margin-right: 7px; }

  .call-pill {
    background: var(--green); color: var(--navy-deep); font-weight: 600;
    border-radius: 10px; white-space: nowrap;
  }
  .call-pill--lg { font-size: 21px; padding: 4px 18px; }
  .call-pill--sm { font-size: 16px; padding: 3px 12px; }

  .visit-line { color: var(--white); }
  .visit-line--lg { font-size: 20px; }
  .visit-line--sm { font-size: 16px; }

  .contact { display: flex; align-items: flex-start; color: var(--white); }
  .contact__phone { font-weight: 700; line-height: 1.05; }
  .contact--lg { gap: 10px; }
  .contact--lg .contact__icon { width: 30px; height: 30px; }
  .contact--lg .contact__phone { font-size: 26px; }
  .contact--lg .contact__web { font-size: 18px; }
  .contact--sm { gap: 8px; }
  .contact--sm .contact__icon { width: 22px; height: 22px; }
  .contact--sm .contact__phone { font-size: 18px; }
  .contact--sm .contact__web { font-size: 14px; }

  .footer-line { color: var(--white); display: flex; align-items: center; white-space: nowrap; }
  .footer-line__email { display: flex; align-items: center; gap: 8px; }
  .footer-line__dot { border: 2px solid var(--green); border-radius: 4px; }
  .footer-line--lg { font-size: 19px; gap: 36px; }
  .footer-line--lg .footer-line__dot { width: 22px; height: 22px; }
  .footer-line--sm { font-size: 14.5px; gap: 24px; }
  .footer-line--sm .footer-line__dot { width: 17px; height: 17px; }
</style>
</head>
<body>

<header class="set-title">
  <div class="set-title__name">Brimlow Plumbing</div>
  <div class="set-title__tagline">Professional Local Services</div>
</header>

<div class="side-label side-label--front">FRONT</div>
<div class="side-label side-label--back">BACK</div>

<!-- Main flyer -->
<article class="flyer flyer--main">
  <svg class="flyer__bg" viewBox="0 0 60 86" preserveAspectRatio="none">
    <polygon points="0,10 30,21 60,7 60,86 0,86" fill="var(--navy)"/>
    <polygon points="0,3 0,7.5 24,16.5 27,15.5" fill="var(--green)"/>
    <polygon points="30,21 60,7 60,11 33,23" fill="var(--navy-soft)"/>
    <polygon points="29,24 60,11 60,76 43,79 33,56" fill="var(--navy-soft)"/>
    <polygon points="0,79 0,86 18,86" fill="var(--green)"/>
    <polygon points="48,86 60,80 60,86" fill="var(--navy-deep)"/>
  </svg>
  <svg class="flyer__bg" viewBox="0 0 60 86" preserveAspectRatio="none" role="img" aria-label="Photo of a smiling plumber in a cap and overalls holding wrenches and pipes">
    <defs>
      <linearGradient id="photoMain" x1="0" y1="0" x2="1" y2="1">
        <stop offset="0" stop-color="#5f9a45"/>
        <stop offset="1" stop-color="#22405f"/>
      </linearGradient>
    </defs>
    <polygon points="31,24.5 60,12.5 60,75 44,77.5 34.5,56" fill="url(#photoMain)"/>
  </svg>

  <div class="flyer__item brand brand--lg" style="left:176px;top:36px;">
    <div class="brand__mark"></div>
    <div class="brand__name"><span>Brimlow</span><span>Plumbing</span><span>Solutions</span></div>
  </div>
  <div class="flyer__item logo-slot logo-slot--lg" style="left:452px;top:38px;">
    <div class="logo-slot__word">LOGO</div>
    <div class="logo-slot__sub">Local choice services</div>
  </div>

  <h1 class="flyer__item headline headline--lg" style="left:42px;top:226px;">Reliable<br>Plumbing.</h1>
  <div class="flyer__item subhead subhead--lg" style="left:42px;top:352px;">Real Solutions.</div>

  <ul class="flyer__item services services--lg" style="left:42px;top:422px;">
    <li>Emergency repairs</li>
    <li>Blocked Drains</li>
    <li>Hot Water Systems</li>
    <li>Maintenance Systems</li>
    <li class="services__cont">Renovations</li>
  </ul>

  <div class="flyer__item call-pill call-pill--lg" style="left:40px;top:600px;">Call [your number]</div>
  <div class="flyer__item visit-line visit-line--lg" style="left:54px;top:640px;">or visit your [website]</div>

  <div class="flyer__item contact contact--lg" style="left:41px;top:704px;">
    <svg class="contact__icon" viewBox="0 0 24 24"><circle cx="12" cy="12" r="12" fill="#7cc142"/><path d="M8.2 6.5c.4-.4 1-.4 1.3 0l1.4 1.8c.3.4.3.9 0 1.3l-.8.9c.7 1.5 1.9 2.7 3.4 3.4l.9-.8c.4-.3.9-.3 1.3 0l1.8 1.4c.4.3.4.9 0 1.3l-1 1c-.6.6-1.5.8-2.3.5-3.2-1.2-5.7-3.7-6.9-6.9-.3-.8-.1-1.7.5-2.3z" fill="#10263f"/></svg>
    <div>
      <div class="contact__phone">+023 5571</div>
      <div class="contact__web">visit [website]</div>
    </div>
  </div>

  <div class="flyer__item footer-line footer-line--lg" style="left:124px;top:784px;">
    <span>Brimlow Plumbing</span>
    <span class="footer-line__email"><span class="footer-line__dot"></span>brimlow@pipemail.com</span>
  </div>
</article>

<!-- Front flyer -->
<article class="flyer flyer--front">
  <svg class="flyer__bg" viewBox="0 0 60 67" preserveAspectRatio="none">
    <polygon points="0,9 30,19 60,6 60,67 0,67" fill="var(--navy)"/>
    <polygon points="0,2.5 0,6.5 22,14 25.5,13" fill="var(--green)"/>
    <polygon points="28,21 60,9 60,62 43,64 32,45" fill="var(--navy-soft)"/>
    <polygon points="0,60 0,67 17,67" fill="var(--green)"/>
  </svg>
  <svg class="flyer__bg" viewBox="0 0 60 67" preserveAspectRatio="none" role="img" aria-label="Photo of a smiling plumber in a cap and overalls holding wrenches">
    <defs>
      <linearGradient id="photoFront" x1="0" y1="0" x2="1" y2="1">
        <stop offset="0" stop-color="#5f9a45"/>
        <stop offset="1" stop-color="#22405f"/>
      </linearGradient>
    </defs>
    <polygon points="30,21.5 60,10.5 60,61 44,63 33.5,45" fill="url(#photoFront)"/>
  </svg>

  <div class="flyer__item brand brand--sm" style="left:152px;top:14px;">
    <div class="brand__mark"></div>
    <div class="brand__name"><span>Brimlow</span><span>Plumbing</span><span>Solutions</span></div>
  </div>
  <div class="flyer__item logo-slot logo-slot--sm" style="left:350px;top:14px;">
    <div class="logo-slot__word">LOGO</div>
    <div class="logo-slot__sub">Local choice services</div>
  </div>

  <h2 class="flyer__item headline headline--sm" style="left:29px;top:132px;">Reliable<br>Plumbing.</h2>
  <div class="flyer__item subhead subhead--sm" style="left:29px;top:220px;">Real Solutions.</div>

  <ul class="flyer__item services services--front" style="left:30px;top:266px;">
    <li>Homeowners</li>
    <li>Residential Repairs</li>
    <li>Real Estate Agents</li>
    <li>Property Managers</li>
    <li class="services__cont">Supports</li>
  </ul>

  <div class="flyer__item call-pill call-pill--sm" style="left:29px;top:388px;">Call [your number]</div>
  <div class="flyer__item visit-line visit-line--sm" style="left:40px;top:418px;">or visit [website]</div>
</article>

<!-- Back flyer -->
<article class="flyer flyer--back">
  <svg class="flyer__bg" viewBox="0 0 60 73" preserveAspectRatio="none">
    <polygon points="0,9 30,19 60,6 60,73 0,73" fill="var(--navy)"/>
    <polygon points="0,2.5 0,6.5 22,14 25.5,13" fill="var(--green)"/>
    <polygon points="28,21 60,9 60,66 43,68 32,48" fill="var(--navy-soft)"/>
    <polygon points="0,66 0,73 17,73" fill="var(--green)"/>
  </svg>
  <svg class="flyer__bg" viewBox="0 0 60 73" preserveAspectRatio="none" role="img" aria-label="Photo of a smiling plumber in a cap and overalls holding wrenches">
    <defs>
      <linearGradient id="photoBack" x1="0" y1="0" x2="1" y2="1">
        <stop offset="0" stop-color="#5f9a45"/>
        <stop offset="1" stop-color="#22405f"/>
      </linearGradient>
    </defs>
    <polygon points="30,21.5 60,10.5 60,65 44,67 33.5,48" fill="url(#photoBack)"/>
  </svg>

  <div class="flyer__item brand brand--sm" style="left:152px;top:14px;">
    <div class="brand__mark"></div>
    <div class="brand__name"><span>Brimlow</span><span>Plumbing</span><span>Solutions</span></div>
  </div>
  <div class="flyer__item logo-slot logo-slot--sm" style="left:350px;top:14px;">
    <div class="logo-slot__word">LOGO</div>
    <div class="logo-slot__sub">Local choice services</div>
  </div>

  <h2 class="flyer__item headline headline--sm" style="left:29px;top:124px;">Reliable<br>Plumbing.</h2>
  <div class="flyer__item subhead subhead--sm" style="left:29px;top:218px;">Real Solutions.</div>

  <ul class="flyer__item services services--back" style="left:35px;top:270px;">
    <li>Blocked Drains</li>
    <li>Hot Water Systems</li>
    <li>Maintenance Plans</li>
    <li>Renovations</li>
  </ul>

  <div class="flyer__item call-pill call-pill--sm" style="left:35px;top:380px;">Call [your number]</div>
  <div class="flyer__item visit-line visit-line--sm" style="left:46px;top:410px;">or visit your [website]</div>

  <div class="flyer__item contact contact--sm" style="left:35px;top:444px;">
    <svg class="contact__icon" viewBox="0 0 24 24"><circle cx="12" cy="12" r="12" fill="#7cc142"/><path d="M8.2 6.5c.4-.4 1-.4 1.3 0l1.4 1.8c.3.4.3.9 0 1.3l-.8.9c.7 1.5 1.9 2.7 3.4 3.4l.9-.8c.4-.3.9-.3 1.3 0l1.8 1.4c.4.3.4.9 0 1.3l-1 1c-.6.6-1.5.8-2.3.5-3.2-1.2-5.7-3.7-6.9-6.9-.3-.8-.1-1.7.5-2.3z" fill="#10263f"/></svg>
    <div>
      <div class="contact__phone">+023 5572</div>
      <div class="contact__web">visit [website]</div>
    </div>
  </div>

  <div class="flyer__item footer-line footer-line--sm" style="left:105px;top:498px;">
    <span>Brimlow Plumbing</span>
    <span class="footer-line__email"><span class="footer-line__dot"></span>brimlow@pipemail.com</span>
  </div>
</article>

</body>
</html>
```